Shine Fox Auto Care Business Card

2 side business card design for an auto detailing business

Target Market(s)

Auto detailing

Contact Information for Business Card

Things included

The business name “Shine Fox Auto Care”
Mark Dunrow
(403)271-6094
Marlow Creek, Sk

Services offered - complete interior& exterior detail
- paint correction & protection
- ceramic coating
- trim restore
- auto carpet & seat cleaning

Requirements
Must have
• Colours that are in my logo

Services offered

My name Mark Dunrow
403-271-6094
Marlow Creek, Sk

Not too sure in what order for these ?
Website. Shinefoxautocare.com
Instagram Shinefoxautocare
Email. Shinefoxautoac@mailvento.com

```html
<!DOCTYPE html>
<html lang="en">
<head>
<meta charset="utf-8">
<title>Shine Fox Auto Care – Business Card</title>
<link href="https://fonts.googleapis.com/css2?family=Arimo:wght@400&family=Michroma&display=swap" rel="stylesheet">
<style>
  :root {
    --page: #0e0e0e;
    --card: #1a1a1a;
    --accent: #a10a0a;
    --text: #ffffff;
    --divider: #4a4a4a;
  }
  * { box-sizing: border-box; margin: 0; padding: 0; }
  html, body { width: 1200px; height: 900px; overflow: hidden; background: var(--page); }
  .canvas {
    width: 1200px; height: 900px;
    display: flex; flex-direction: column; align-items: center; justify-content: center; gap: 36px;
  }
  .card {
    position: relative;
    width: 700px; height: 400px;
    background: var(--card);
    display: flex;
    box-shadow: 0 12px 30px rgba(0,0,0,.6);
  }
  .card::after {
    content: ""; position: absolute; left: 0; right: 0; bottom: 0; height: 9px; background: var(--accent);
  }
  .card__brand {
    width: 46%;
    display: flex; align-items: center; justify-content: center;
  }
  .card__divider {
    width: 1px; margin: 70px 0 60px; background: var(--divider);
  }
  .card__info {
    flex: 1; display: flex; flex-direction: column; justify-content: center; padding-left: 38px;
  }
  .brand {
    display: flex; flex-direction: column; align-items: center; gap: 14px;
  }
  .brand__dot {
    width: 58px; height: 58px; border-radius: 50%; border: 5px solid var(--accent);
  }
  .brand__name {
    font-family: "Michroma", sans-serif; font-size: 19px; color: var(--text);
    text-align: center; line-height: 1.45; letter-spacing: 1px;
  }
  .services { list-style: none; }
  .services li {
    font-family: "Arimo", sans-serif; font-size: 19px; color: var(--text);
    line-height: 1.55; padding-left: 18px; position: relative;
  }
  .services li::before {
    content: ""; position: absolute; left: 0; top: 10px; width: 7px; height: 7px; border-radius: 50%; background: var(--accent);
  }
  .person {
    font-family: "Michroma", sans-serif; font-size: 24px; font-weight: 400; color: var(--accent);
    letter-spacing: 1px; margin-bottom: 20px; text-transform: uppercase;
  }
  .contacts { list-style: none; }
  .contacts li {
    display: flex; align-items: center; gap: 12px;
    font-family: "Arimo", sans-serif; font-size: 18px; color: var(--text); line-height: 1; margin-bottom: 11px;
  }
  .contacts svg { width: 22px; height: 22px; flex: none; }
</style>
</head>
<body>
<main class="canvas">
  <section class="card card--front">
    <div class="card__brand">
      <div class="brand">
        <span class="brand__dot"></span>
        <span class="brand__name">SHINE FOX<br>AUTO CARE</span>
      </div>
    </div>
    <div class="card__divider"></div>
    <div class="card__info">
      <ul class="services">
        <li>Paint correction &amp; protection</li>
        <li>Ceramic coating</li>
        <li>Trim restore</li>
        <li>Auto carpet &amp; seat cleaning</li>
      </ul>
    </div>
  </section>

  <section class="card card--back">
    <div class="card__brand">
      <div class="brand">
        <span class="brand__dot"></span>
        <span class="brand__name">SHINE FOX<br>AUTO CARE</span>
      </div>
    </div>
    <div class="card__divider"></div>
    <div class="card__info">
      <h1 class="person">Mark Dunrow</h1>
      <ul class="contacts">
        <li>
          <svg viewBox="0 0 24 24"><circle cx="12" cy="12" r="12" fill="#a10a0a"/><path d="M8.5 6.5l2 2-1.2 1.5c.8 1.7 2 2.9 3.7 3.7l1.5-1.2 2 2-1.5 1.8c-3.8-.6-7.7-4.5-8.3-8.3z" fill="#1a1a1a"/></svg>
          (403)271-6094
        </li>
        <li>
          <svg viewBox="0 0 24 24"><circle cx="12" cy="12" r="12" fill="#a10a0a"/><rect x="6" y="8" width="12" height="8" fill="#1a1a1a"/><path d="M6 8l6 5 6-5" stroke="#a10a0a" stroke-width="1.3" fill="none"/></svg>
          Shinefoxautocare@mailvento.com
        </li>
        <li>
          <svg viewBox="0 0 24 24"><circle cx="12" cy="12" r="12" fill="#a10a0a"/><g stroke="#1a1a1a" stroke-width="1.3" fill="none"><circle cx="12" cy="12" r="6"/><ellipse cx="12" cy="12" rx="2.6" ry="6"/><path d="M6 12h12"/></g></svg>
          www.Shinefoxautocare.com
        </li>
        <li>
          <svg viewBox="0 0 24 24"><circle cx="12" cy="12" r="12" fill="#a10a0a"/></svg>
          Shinefoxautocare
        </li>
        <li>
          <svg viewBox="0 0 24 24"><circle cx="12" cy="12" r="12" fill="#a10a0a"/><path d="M12 5.5a4.5 4.5 0 0 0-4.5 4.5c0 3.3 4.5 8.5 4.5 8.5s4.5-5.2 4.5-8.5A4.5 4.5 0 0 0 12 5.5z" fill="#1a1a1a"/><circle cx="12" cy="10" r="1.6" fill="#a10a0a"/></svg>
          Marlow Creek, Sk
        </li>
      </ul>
    </div>
  </section>
</main>
</body>
</html>
```